Every Shelf Set Neatly or ESN Organized needs a business card design. ESN Organized is a professi

We need a business card design that is clean, sharp and conveys a sense of organization. I already have a logo.

Target Market(s)

Families (specifically mothers), small business owners, parents, seniors

Industry/Entity Type

Business

Contact Information for Business Card

My website is www.esnorganized-example.com and my Facebook page is http://www.sociallink-example.com/everyshelfsetneatly. The phone number is 418-552-7094 and I want to be listed as Lorna M. Pelham, Owner

Requirements
Must have
• My logo.

```html
<!DOCTYPE html>
<html lang="en">
<head>
<meta charset="utf-8">
<title>Every Shelf Set Neatly — Business Card</title>
<link href="https://fonts.googleapis.com/css2?family=Roboto:wght@400&display=swap" rel="stylesheet">
<style>
  :root {
    --backdrop: #e9e6e1;
    --card: #fbfbfb;
    --brand-blue: #3f86c6;
    --rule-blue: #5a9bd3;
    --ink: #1d1d1d;
    --muted: #4a4a4a;
    --tab: #1a1a1a;
  }
  * { box-sizing: border-box; margin: 0; padding: 0; }
  html, body {
    width: 1200px; height: 1022px; overflow: hidden;
    background: var(--backdrop);
    font-family: "Roboto", Arial, sans-serif;
  }
  .canvas {
    width: 1200px; height: 1022px;
    display: flex; flex-direction: column; align-items: center; justify-content: center;
    gap: 56px;
  }
  .card {
    position: relative;
    width: 700px; height: 400px;
    background: var(--card);
    border-radius: 18px;
    box-shadow: 0 6px 18px rgba(0,0,0,0.12);
    overflow: hidden;
  }

  /* Shared brand name: one colour, one weight */
  .brand {
    display: flex; align-items: center; gap: 12px;
  }
  .brand-mark {
    width: 12px; height: 12px; background: var(--brand-blue); flex: none;
  }
  .brand-name {
    font-size: 28px; font-weight: 400; color: var(--brand-blue);
  }

  /* Front */
  .card-front .brand {
    position: absolute; left: 52px; top: 50px;
  }
  .edge-tab {
    position: absolute; left: 0; top: 200px;
    width: 26px; height: 74px; background: var(--tab);
  }
  .person-name {
    position: absolute; left: 52px; top: 186px;
    font-size: 30px; font-weight: 400; color: var(--brand-blue);
  }
  .divider {
    position: absolute; left: 52px; right: 52px; top: 238px;
    height: 1.5px; background: var(--rule-blue);
  }
  .person-role {
    position: absolute; left: 52px; top: 247px;
    font-size: 17px; color: var(--muted);
  }
  .contact {
    position: absolute; left: 52px; top: 292px;
    list-style: none; display: flex; flex-direction: column; gap: 9px;
  }
  .contact li {
    display: flex; align-items: center; gap: 12px;
    font-size: 17px; color: var(--ink);
  }
  .contact svg { width: 14px; height: 14px; flex: none; }

  /* Back */
  .card-back .brand {
    position: absolute; left: 0; right: 0; top: 176px;
    justify-content: center;
  }
  .back-rule {
    position: absolute; left: 52px; right: 52px; top: 238px;
    height: 1.5px; background: var(--rule-blue);
  }
</style>
</head>
<body>
<main class="canvas">

  <section class="card card-front">
    <div class="brand">
      <span class="brand-mark"></span>
      <span class="brand-name">Every Shelf Set Neatly</span>
    </div>
    <div class="edge-tab"></div>
    <p class="person-name">Lorna M. Pelham</p>
    <div class="divider"></div>
    <p class="person-role">Owner</p>
    <ul class="contact">
      <li>
        <svg viewBox="0 0 14 14" aria-hidden="true"><path d="M3 1 L5 1 L6 4 L4.5 5.2 Q5.8 8 8.8 9.5 L10 8 L13 9 L13 11 Q12 13 10 13 Q2 11 1 3 Q1 1 3 1Z" fill="var(--rule-blue)"/></svg>
        418-552-7094
      </li>
      <li>
        <svg viewBox="0 0 14 14" aria-hidden="true"><circle cx="7" cy="7" r="6" fill="none" stroke="var(--rule-blue)" stroke-width="1.3"/><ellipse cx="7" cy="7" rx="2.6" ry="6" fill="none" stroke="var(--rule-blue)" stroke-width="1.1"/><line x1="1" y1="7" x2="13" y2="7" stroke="var(--rule-blue)" stroke-width="1.1"/></svg>
        www.esnorganized-example.com
      </li>
      <li>
        <svg viewBox="0 0 14 14" aria-hidden="true"><circle cx="7" cy="7" r="5" fill="var(--rule-blue)"/></svg>
        www.sociallink-example.com/everyshelfsetneatly
      </li>
    </ul>
  </section>

  <section class="card card-back">
    <div class="brand">
      <span class="brand-mark"></span>
      <span class="brand-name">Every Shelf Set Neatly</span>
    </div>
    <div class="back-rule"></div>
  </section>

</main>
</body>
</html>
```